Business Card Design Project

After recently finishing a design project for the company logo using markbazaar, it's now time for a business card. Attached to this is the logo.

The requirements for the business card are pretty straightforward:

- A clean, uncomplicated look
- Consistent usage of fonts
- Designs for both single sided and double sided cards
- A modern layout with preferably space to refer to social media accounts and/or downloadable vcards through a qr code
- consistent application of the company colour scheme: red/white. Hex codes for exact colour can be provided

Thanks!

```html
<!DOCTYPE html>
<html lang="en">
<head>
<meta charset="utf-8">
<title>Stone Path Recruiting – Business Card</title>
<link rel="stylesheet" href="https://fonts.googleapis.com/css2?family=Source+Sans+3:wght@400;600;700&display=swap">
<style>
  :root {
    --backdrop: #e9e7e4;
    --card: #ffffff;
    --ink: #231f20;
    --brand-red: #e31e24;
    --rule: #231f20;
  }
  * { box-sizing: border-box; margin: 0; padding: 0; }
  html, body {
    width: 960px;
    height: 1200px;
    overflow: hidden;
  }
  body {
    position: relative;
    background: var(--backdrop);
    font-family: "Source Sans 3", sans-serif;
    color: var(--ink);
  }
  .card {
    position: absolute;
    left: 55px;
    width: 840px;
    height: 479px;
    background: var(--card);
    border-radius: 28px;
  }
  .card--front { top: 73px; }
  .card--back { top: 638px; }

  /* Front: brand */
  .brand {
    position: absolute;
    left: 0;
    right: 0;
    top: 150px;
    display: flex;
    justify-content: center;
    align-items: center;
    gap: 22px;
  }
  .brand__mark {
    width: 40px;
    height: 40px;
    background: var(--brand-red);
  }
  .brand__name {
    font-size: 62px;
    font-weight: 600;
    line-height: 1;
    color: var(--ink);
    letter-spacing: -0.5px;
  }

  /* Front: person */
  .person {
    position: absolute;
    left: 39px;
    top: 305px;
  }
  .person__name {
    font-size: 27px;
    font-weight: 700;
    line-height: 32px;
  }
  .person__role {
    font-size: 21px;
    font-weight: 400;
    line-height: 28px;
  }
  .divider {
    position: absolute;
    left: 39px;
    right: 22px;
    top: 387px;
    border-top: 2px solid var(--rule);
  }

  /* Front: contacts */
  .contact {
    position: absolute;
    font-size: 21px;
    line-height: 28px;
    display: flex;
    align-items: center;
    gap: 8px;
  }
  .contact svg { width: 15px; height: 15px; fill: var(--ink); flex: none; }
  .contact--phone { left: 39px; top: 435px; }
  .contact--email { left: 260px; top: 401px; }
  .contact--web { left: 260px; top: 435px; }
  .address {
    position: absolute;
    right: 29px;
    top: 407px;
    text-align: right;
    font-size: 21px;
    line-height: 28px;
  }

  /* Back */
  .back-brand {
    position: absolute;
    inset: 0;
    display: flex;
    justify-content: center;
    align-items: center;
    gap: 24px;
  }
  .back-brand__mark {
    width: 56px;
    height: 56px;
    background: var(--brand-red);
  }
  .back-brand__name {
    font-size: 58px;
    font-weight: 600;
    color: var(--brand-red);
    line-height: 1;
  }
</style>
</head>
<body>

  <section class="card card--front">
    <div class="brand">
      <span class="brand__mark"></span>
      <span class="brand__name">Stone Path Recruiting</span>
    </div>

    <div class="person">
      <p class="person__name">Your Name</p>
      <p class="person__role">Designation</p>
    </div>

    <div class="divider"></div>

    <p class="contact contact--phone">
      <svg viewBox="0 0 16 16" aria-hidden="true"><path d="M1 6c0-2 3-4 7-4s7 2 7 4v1h-4V5.5H5V7H1zM4 8h8l2 6H2z"/></svg>
      123-123-1234
    </p>
    <p class="contact contact--email">
      <svg viewBox="0 0 16 16" aria-hidden="true"><path d="M1 3h14v10H1zm1.5 1.5v.3L8 9l5.5-4.2v-.3zM2.5 6.7v4.8h11V6.7L8 11z"/></svg>
      info@yourwebsite.com
    </p>
    <p class="contact contact--web">
      <svg viewBox="0 0 16 16" aria-hidden="true"><circle cx="8" cy="8" r="6.5"/></svg>
      www.stonepath.com
    </p>

    <p class="address">1234, Street Name<br>District, City, Country Code.</p>
  </section>

  <section class="card card--back">
    <div class="back-brand">
      <span class="back-brand__mark"></span>
      <span class="back-brand__name">Stone Path</span>
    </div>
  </section>

</body>
</html>
```